Trabworth Business Cards

We need a business card design for Trabworth Mining.

This is a B2B company that buys and sells large machinery tires within the coal mining industry. The design should the strong, crisp and masculine. I have uploaded the company logo and rough mock-up of what the back of the card should look like. the front of the card should have the same look/feel as the back. I need editable templates for both the front and the back of the card.

Color scheme should be grey/green/black

Contact information to include on the card:
Name: Dale Pembrose
Title: Managing Director
Phone: 555-314-2069
Address: 1187 Welford #3 Dallas, TX 75290
Email: Dale@Trabworth-example.com

I am also opening a contest for letterhead design. If you submit a business card design, please also submit a letterhead design with the same look/feel. The winner of the business card design will also will the letter head and be paid for both.

Target Market(s)

Procurement men/women in the coal mining industry

Industry/Entity Type

Coal Mining

```html
<!DOCTYPE html>
<html lang="en">
<head>
<meta charset="utf-8">
<title>Trabworth Mining – Business Card</title>
<link rel="stylesheet" href="https://fonts.googleapis.com/css2?family=Open+Sans:wght@400;600;700&display=swap">
<style>
  :root {
    --canvas: #e4e4e2;
    --card: #0b0b0b;
    --green: #6cb43f;
    --white: #ffffff;
    --grey: #d9d9d9;
    --shadow: rgba(0,0,0,.28);
  }
  * { box-sizing: border-box; margin: 0; padding: 0; }
  html, body { width: 1200px; height: 1024px; overflow: hidden; }
  body { background: var(--canvas); position: relative; font-family: "Open Sans", Arial, sans-serif; }

  .card {
    position: absolute;
    background: var(--card);
    overflow: hidden;
    box-shadow: 0 10px 30px var(--shadow);
  }
  .card svg.shapes { position: absolute; inset: 0; }

  .brand {
    position: absolute;
    display: flex; align-items: center; gap: 10px;
    color: var(--white); font-weight: 700; white-space: nowrap;
  }
  .brand__square { width: 18px; height: 18px; background: var(--green); flex: none; }

  /* Front */
  .card--front { left: 15px; top: 302px; width: 740px; height: 420px; }
  .card--front .brand { left: 36px; top: 186px; font-size: 24px; letter-spacing: 1px; }
  .holder { position: absolute; right: 36px; top: 44px; text-align: right; }
  .holder__name { color: var(--white); font-weight: 700; font-size: 22px; line-height: 1.2; }
  .holder__title { color: var(--green); font-size: 15px; margin-top: 2px; }
  .address {
    position: absolute; left: 390px; top: 336px;
    color: var(--white); font-size: 14px; line-height: 1.6; white-space: nowrap;
  }
  .divider { position: absolute; left: 520px; top: 334px; width: 1px; height: 50px; background: var(--grey); }
  .contact {
    position: absolute; left: 534px; top: 336px;
    color: var(--white); font-size: 12px; line-height: 1.9; white-space: nowrap;
  }
  .contact__row { display: flex; align-items: center; gap: 6px; }
  .contact__row svg { width: 13px; height: 13px; flex: none; }

  /* Back */
  .card--back { left: 790px; top: 180px; width: 380px; height: 665px; }
  .card--back .brand { left: 0; right: 0; top: 440px; justify-content: center; font-size: 26px; letter-spacing: 1px; }
</style>
</head>
<body>

  <section class="card card--front" aria-label="Business card front">
    <svg class="shapes" width="740" height="420" viewBox="0 0 740 420" aria-hidden="true">
      <polygon points="420,0 470,0 350,420 300,420" fill="var(--green)"/>
      <polygon points="326,330 376,330 350,420 300,420" fill="var(--white)"/>
    </svg>

    <div class="brand"><span class="brand__square"></span><span>Trabworth Mining</span></div>

    <div class="holder">
      <div class="holder__name">Dale Pembrose</div>
      <div class="holder__title">Managing Director</div>
    </div>

    <div class="address">1187 Welford #3<br>Dallas, TX 75290</div>
    <div class="divider"></div>
    <div class="contact">
      <div class="contact__row">
        <svg viewBox="0 0 24 24"><path fill="var(--green)" d="M6.6 10.8a15 15 0 0 0 6.6 6.6l2.2-2.2a1 1 0 0 1 1-.25 11.4 11.4 0 0 0 3.6.6 1 1 0 0 1 1 1V20a1 1 0 0 1-1 1A17 17 0 0 1 3 4a1 1 0 0 1 1-1h3.5a1 1 0 0 1 1 1 11.4 11.4 0 0 0 .6 3.6 1 1 0 0 1-.25 1z"/></svg>
        <span>555-314-2069</span>
      </div>
      <div class="contact__row">
        <svg viewBox="0 0 24 24"><rect x="2" y="5" width="20" height="14" fill="var(--green)"/><path d="M2 5l10 8 10-8" fill="none" stroke="var(--card)" stroke-width="2"/></svg>
        <span>Dale@Trabworth-example.com</span>
      </div>
    </div>
  </section>

  <section class="card card--back" aria-label="Business card back">
    <svg class="shapes" width="380" height="665" viewBox="0 0 380 665" aria-hidden="true">
      <polygon points="0,145 380,38 380,104 0,211" fill="var(--green)"/>
      <polygon points="315,190 380,190 380,315" fill="var(--green)"/>
    </svg>
    <div class="brand"><span class="brand__square"></span><span>Trabworth Mining</span></div>
  </section>

</body>
</html>
```